Stonebrace Business Card Design

The Stonebrace Co is an aggregate (crushing) equipment dealer serving Western Canadian provinces. Stonebrace is a distributor of aggregate equipment for different manufacturers.

We are looking to change and update the existing business card which has been used since the existence of the company. A copy of existing card has been attached for reference. The Stonebrace Co logo we want to remain the same and we want the green color to remain the same.

We are wanting something new with a different look. A refreshing card to show a new modern and updated look. No longer wanting to have the manufacturers on the back of the card but something more like our logo on the back of the card with a statement like "Crushing Solutions"

ideas could be:
- card can be different colors on front and back
- front or reverse of the card could possibly be the green color with the logo in black

Target Market(s)

Owners of Aggregate/Crushing companies

Contact Information for Business Card

see above

Requirements
Must have
• - logo to remain same along with same font within logo
• - green color to remain same
Nice to have
• as noted above under project description
Should not have

```html
<!DOCTYPE html>
<html lang="en">
<head>
<meta charset="utf-8">
<title>Stonebrace Business Card</title>
<link rel="stylesheet" href="https://fonts.googleapis.com/css2?family=Arimo:wght@400;700&display=swap">
<style>
  :root {
    --brand-green: #8a8d0b;
    --ink: #222222;
    --card-white: #ffffff;
    --backdrop: #ecebe8;
  }
  html, body {
    margin: 0;
    padding: 0;
    width: 1200px;
    height: 900px;
    overflow: hidden;
    background: var(--backdrop);
    font-family: "Arimo", Arial, sans-serif;
  }
  .canvas {
    position: relative;
    width: 1200px;
    height: 900px;
  }
  .card {
    position: absolute;
    box-shadow: 0 6px 18px rgba(0,0,0,0.12);
  }
  .card-front {
    left: 150px;
    top: 80px;
    width: 588px;
    height: 363px;
    background: var(--card-white);
  }
  .front-mark {
    position: absolute;
    left: 62px;
    top: 115px;
    width: 120px;
    text-align: center;
    color: var(--brand-green);
    font-weight: 700;
    font-size: 19px;
  }
  .front-mark .mark-dot {
    display: block;
    width: 84px;
    height: 84px;
    margin: 0 auto 12px;
    border-radius: 50%;
    background: var(--brand-green);
  }
  .holder-name {
    position: absolute;
    left: 254px;
    top: 66px;
    margin: 0;
    font-size: 22px;
    font-weight: 400;
    letter-spacing: 0.3px;
    color: var(--brand-green);
  }
  .contact-list {
    position: absolute;
    left: 258px;
    top: 114px;
    margin: 0;
    padding: 0;
    list-style: none;
    font-size: 16px;
    line-height: 21.4px;
    color: var(--ink);
  }
  .contact-list li {
    display: flex;
    align-items: center;
    gap: 4px;
  }
  .contact-list svg {
    width: 15px;
    height: 13px;
    fill: var(--brand-green);
    flex: none;
  }
  .company-address {
    position: absolute;
    left: 258px;
    top: 242px;
    margin: 0;
    font-style: normal;
    font-size: 16px;
    line-height: 22px;
    color: var(--ink);
  }
  .company-address strong { font-weight: 700; }

  .card-back {
    left: 388px;
    top: 505px;
    width: 567px;
    height: 352px;
    background: var(--brand-green);
    color: var(--ink);
    text-align: center;
  }
  .back-mark {
    display: block;
    width: 80px;
    height: 80px;
    margin: 100px auto 0;
    border-radius: 50%;
    background: var(--ink);
  }
  .company-name {
    margin: 24px 0 0;
    font-size: 30px;
    font-weight: 700;
    letter-spacing: 0.5px;
  }
  .tagline {
    display: flex;
    align-items: center;
    justify-content: center;
    gap: 10px;
    margin-top: 10px;
    font-size: 15px;
    font-weight: 700;
    letter-spacing: 0.6px;
  }
  .tagline::before, .tagline::after {
    content: "";
    width: 68px;
    height: 1.5px;
    background: var(--ink);
  }
</style>
</head>
<body>
<main class="canvas">
  <section class="card card-front" aria-label="Card front">
    <div class="front-mark"><span class="mark-dot"></span>Stonebrace</div>
    <h1 class="holder-name">DANA MORROW</h1>
    <ul class="contact-list">
      <li><svg viewBox="0 0 15 13"><path d="M1 4c0-2 3-3 6.5-3S14 2 14 4v1h-3V4H4v1H1z M3 6h9l2 6H1z"/></svg>780.555.0141(Direct)</li>
      <li><svg viewBox="0 0 15 13"><path d="M1 4c0-2 3-3 6.5-3S14 2 14 4v1h-3V4H4v1H1z M3 6h9l2 6H1z"/></svg>780.555.0172</li>
      <li><svg viewBox="0 0 15 13"><path d="M4 0h6v4H4z M1 5h13v8H1z M3 7h3v2H3z"/></svg>780.555.0193</li>
      <li><svg viewBox="0 0 15 13"><path d="M1 2h13v9H1z" /><path d="M1 2l6.5 5L14 2" stroke="#fff" stroke-width="1.2" fill="none"/></svg>dana@stonebr.com</li>
      <li><svg viewBox="0 0 15 13"><circle cx="7.5" cy="6.5" r="6"/><path d="M4 4h3v3H5z M9 8h2v2H9z" fill="#fff"/></svg>www.stonebrace.ca</li>
    </ul>
    <address class="company-address">
      <strong>The Stonebrace Co.</strong><br>
      2210-48B Avenue<br>
      Camrose, Alberta T4V 2B7
    </address>
  </section>

  <section class="card card-back" aria-label="Card back">
    <span class="back-mark"></span>
    <h2 class="company-name">THE STONEBRACE CO.</h2>
    <div class="tagline">CRUSHING SOLUTIONS</div>
  </section>
</main>
</body>
</html>
```